Maplecrest Disability - Social Security Disability Attorneys

Our company is expanding to attract clients nationwide for our social security disability practice. We have a logo, but I am looking for a creative and elegant letterhead that projects an image of being technologically advanced but still professional enough for the legal field. I am looking for the "wow factor" combined with this is still professional enough for a law practice.

Requesting letterhead and business card design
Updates

Had to update and change the logo. The previous logo had a typo. Please send updates with the new logo for consideration. The letterhead and business cards should be professional enough to be used for a law firm. Thanks.

Industry/Entity Type

Law Practice, Law Firm, Healthcare Industry, Government

Colors

Designer to choose colors to be used in the design.

Requirements
Nice to have
• **Please create a vertical design for the business card**

```html
<!DOCTYPE html>
<html lang="en">
<head>
<meta charset="utf-8">
<title>Maplecrest Disability Letterhead</title>
<link rel="stylesheet" href="https://fonts.googleapis.com/css2?family=Lato:wght@400;700&family=Dancing+Script:wght@500&display=swap">
<style>
  :root {
    --backdrop: #dedede;
    --paper: #ffffff;
    --ink: #2b2b2b;
    --brand-blue: #4a72e4;
    --brand-orange: #f7852c;
  }
  * { margin: 0; padding: 0; box-sizing: border-box; }
  html, body { width: 1200px; height: 800px; overflow: hidden; }
  body {
    background: var(--backdrop);
    font-family: "Lato", Arial, sans-serif;
    color: var(--ink);
    position: relative;
  }
  .sheet {
    position: absolute;
    top: 111px;
    width: 413px;
    height: 575px;
    background: var(--paper);
    overflow: hidden;
  }
  .sheet--letter { left: 165px; }
  .sheet--blank { left: 611px; }

  .brand {
    position: absolute;
    left: 23px;
    top: 50px;
    display: flex;
    align-items: center;
    gap: 6px;
  }
  .brand__dot {
    width: 9px; height: 9px; border-radius: 50%;
    background: var(--brand-orange);
  }
  .brand__name {
    font-size: 10.5px;
    font-weight: 700;
    letter-spacing: 1.2px;
    text-transform: uppercase;
    color: var(--brand-blue);
  }

  .contact {
    position: absolute;
    left: 290px;
    top: 27px;
    border-left: 1px solid var(--brand-orange);
    padding-left: 5px;
    font-size: 6.6px;
    line-height: 9.7px;
    color: #1f1f1f;
  }
  .contact__address { margin-bottom: 2px; }
  .contact__row { display: flex; align-items: center; gap: 4px; }
  .contact__row svg { width: 7px; height: 7px; flex: none; }

  .letter {
    position: absolute;
    left: 23px;
    top: 119px;
    width: 367px;
    font-size: 8px;
    line-height: 9.4px;
  }
  .letter__date { font-size: 8.6px; margin-bottom: 10px; }
  .letter__block { margin-bottom: 10px; }
  .letter__greeting { font-size: 10px; font-weight: 700; margin: 12px 0 9px; color: #333; }
  .letter__para { text-align: justify; margin-bottom: 9px; }
  .letter__closing { margin-top: 20px; }
  .letter__signature {
    font-family: "Dancing Script", cursive;
    font-size: 20px;
    margin-top: 10px;
    color: #222;
  }

  .footer-band {
    position: absolute;
    left: 0; bottom: 0;
    width: 413px; height: 28px;
  }
</style>
</head>
<body>

<section class="sheet sheet--letter">
  <div class="brand">
    <span class="brand__dot"></span>
    <span class="brand__name">Maplecrest Disability</span>
  </div>

  <address class="contact" style="font-style:normal">
    <div class="contact__address">Suite 4,level 12,Harbour<br>Lane Brisbane QLD 4000</div>
    <div class="contact__row">
      <svg viewBox="0 0 10 10"><path d="M2 1l2 2-1 1.2c.6 1.2 1.6 2.2 2.8 2.8L7 6l2 2-1.4 1.4C4.5 9 1 5.5.6 2.4z" fill="var(--brand-orange)"/></svg>
      <span>555-014-2290</span>
    </div>
    <div class="contact__row">
      <svg viewBox="0 0 10 10"><rect x="0.5" y="2" width="9" height="6" fill="var(--brand-orange)"/><path d="M.5 2l4.5 3.5L9.5 2" stroke="#fff" stroke-width="0.8" fill="none"/></svg>
      <span>Info@maplecrestdisability.com</span>
    </div>
    <div class="contact__row">
      <svg viewBox="0 0 10 10"><circle cx="5" cy="5" r="4.5" fill="var(--brand-orange)"/><path d="M.5 5h9M5 .5c-2 2.5-2 6.5 0 9M5 .5c2 2.5 2 6.5 0 9" stroke="#fff" stroke-width="0.6" fill="none"/></svg>
      <span>www.maplecrestdisability.com</span>
    </div>
  </address>

  <article class="letter">
    <p class="letter__date">January-03-2020</p>
    <p class="letter__block">Mr, Alan Reed<br>President</p>
    <p class="letter__block">Birchline Corporation<br>123 Street Name, Suite# 10<br>City, State, 120023</p>
    <h2 class="letter__greeting">Dear Mr, Alan</h2>
    <p class="letter__para">Lorem ipsum dolor sit amet, consectetur adipisicing elit, sed do eiusmod tempor incididunt ut labore et dolore magna aliqua. Ut enim ad minim veniam, quis nostrud exercitation ullamco laboris nisi ut aliquip ex ea commodo consequat. Duis aute irure dolor in reprehenderit in voluptate velit esse cillum dolore eu fugiat nulla pariatur.</p>
    <p class="letter__para">Lorem ipsum dolor sit amet, consectetur adipisicing elit, sed do eiusmod tempor incididunt ut labore et dolore magna aliqua. Ut enim ad minim veniam, quis nostrud exercitation ullamco laboris nisi ut aliquip ex ea commodo consequat. Duis aute irure dolor in reprehenderit in voluptate velit esse cillum dolore eu fugiat nulla pariatur.</p>
    <p class="letter__para">Lorem ipsum dolor sit amet, consectetur adipisicing elit, sed do eiusmod tempor incididunt ut labore et dolore magna aliqua. Ut enim ad minim veniam, quis nostrud exercitation ullamco laboris nisi ut aliquip ex ea commodo consequat.</p>
    <p class="letter__para">Excepteur sint occaecat cupidatat non proident, sunt in culpa qui officia deserunt mollit anim id est laborum. re et dolore magnam aliquam quaerat voluptatem.</p>
    <p class="letter__closing">Regards</p>
    <p class="letter__signature">Daniel Hart</p>
  </article>

  <svg class="footer-band" viewBox="0 0 413 28" preserveAspectRatio="none">
    <polygon points="0,11 219,11 203,28 0,28" fill="var(--brand-orange)"/>
    <polygon points="232,0 413,0 413,28 208,28" fill="var(--brand-blue)"/>
  </svg>
</section>

<section class="sheet sheet--blank">
  <div class="brand">
    <span class="brand__dot"></span>
    <span class="brand__name">Maplecrest Disability</span>
  </div>

  <address class="contact" style="font-style:normal">
    <div class="contact__address">Suite 4,level 12,Harbour<br>Lane Brisbane QLD 4000</div>
    <div class="contact__row">
      <svg viewBox="0 0 10 10"><path d="M2 1l2 2-1 1.2c.6 1.2 1.6 2.2 2.8 2.8L7 6l2 2-1.4 1.4C4.5 9 1 5.5.6 2.4z" fill="var(--brand-orange)"/></svg>
      <span>555-014-2290</span>
    </div>
    <div class="contact__row">
      <svg viewBox="0 0 10 10"><rect x="0.5" y="2" width="9" height="6" fill="var(--brand-orange)"/><path d="M.5 2l4.5 3.5L9.5 2" stroke="#fff" stroke-width="0.8" fill="none"/></svg>
      <span>Info@maplecrestdisability.com</span>
    </div>
    <div class="contact__row">
      <svg viewBox="0 0 10 10"><circle cx="5" cy="5" r="4.5" fill="var(--brand-orange)"/><path d="M.5 5h9M5 .5c-2 2.5-2 6.5 0 9M5 .5c2 2.5 2 6.5 0 9" stroke="#fff" stroke-width="0.6" fill="none"/></svg>
      <span>www.maplecrestdisability.com</span>
    </div>
  </address>
</section>

</body>
</html>
```